Lumen Ridge Tri-Fold Brochure - Recovering From Alzheimer's

Design a brochure a brochure for Lumen Ridge. www.lumenridge-example.org. We help people with Alzheimer's, or who have had a Traumatic Brain Injury, Concussion or Stroke stop their cognitive decline, and actually reverse decline and improve their cognitive abilities. We use an individualized approach, utilizing extensive lab work and developing a roadmap that includes diet, supplementation, theraputic devices all guided by a Memory Coach. I would like to see a design with pictures of people similar to the demographic on the website. Also incorporate some of the colors from my logo. We offer hope to people who consistently hear, "There is nothing we can do. Alzheimer's is a fatal disease." NOT TRUE! We see people's lives change every day!!!!

Target Market(s)

People who ARE or know someone suffering from cognitive decline, Alzheimer's, Traumatic Brain Injury, Concussion or Stroke.

Industry/Entity Type

Health and wellbeing -- Treating Alzheimer's.

Font styles to use
Other font styles liked:
• Calibri or I think it's called Lota

Colors
0054AA
0677BA
7BADD7
CADEEF
E8F1F8
0094D4
00A9DD
6FCCEA
C7EBF8
E9F6FB
00AB8E
00BBA5
67D7C9
C6EFE9
E9F9F6

Requirements
Must have
• Easily read material (think older eyes) and people between the ages of 40-70. Needs to have a professional feel but not clinical. Create trust and a feeling of caring and hope.
Nice to have
• Please check out my website: www.lumenridge-example.org for content and feel.
Should not have
• Youthful people exercising OR highly stereotypical ageist photos or info.

```html
<!DOCTYPE html>
<html lang="en">
<head>
<meta charset="utf-8">
<title>Lumen Ridge Tri-Fold Brochure</title>
<link rel="stylesheet" href="https://fonts.googleapis.com/css2?family=Libre+Baskerville:wght@400;700&family=Lato:wght@400;700;900&display=swap">
<style>
  :root {
    --stage: #e9ecef;
    --brand-green: #1f9a1f;
    --brand-blue: #0677ba;
    --deep-blue: #0054aa;
    --sky-blue: #7badd7;
    --pale-blue: #e8f1f8;
    --paper: #ffffff;
    --ink: #222222;
    --wheat-light: #f6f1e2;
    --wheat-mid: #e7dcc0;
  }
  * { box-sizing: border-box; margin: 0; padding: 0; }
  html, body { width: 900px; height: 1200px; overflow: hidden; }
  body { background: var(--stage); position: relative; font-family: "Lato", Arial, sans-serif; color: var(--ink); }

  .brochure {
    position: absolute; left: 30px; top: 277px; width: 840px; height: 646px;
    background: var(--paper); overflow: hidden;
    box-shadow: 0 14px 30px rgba(0,0,0,.25);
  }
  .brochure svg.shapes { position: absolute; inset: 0; }

  .panel { position: absolute; top: 0; height: 646px; }
  .panel-inside-left { left: 0; width: 272px; }
  .panel-inside-mid { left: 272px; width: 278px; }
  .panel-cover { left: 550px; width: 290px; }

  .brain-copy { position: absolute; left: 18px; right: 18px; top: 352px; color: var(--paper); text-align: center; }
  .brain-copy .kicker { font-size: 14px; font-weight: 700; letter-spacing: .5px; }
  .brain-copy .headline { font-size: 25px; font-weight: 700; letter-spacing: 1px; margin: 2px 0 10px; }
  .brain-copy .body { font-size: 10px; line-height: 1.35; text-align: justify; }
  .brain-copy .closing { font-size: 13px; font-weight: 700; margin-top: 18px; letter-spacing: .3px; }

  .hope-copy { position: absolute; left: 0; right: 0; top: 326px; text-align: center; font-family: "Libre Baskerville", Georgia, serif; }
  .hope-copy .myth { font-size: 10px; font-weight: 700; color: var(--brand-green); }
  .hope-copy .myth-line { font-size: 16px; color: var(--brand-blue); margin-top: 2px; }
  .hope-copy .rebuttal { font-size: 34px; font-weight: 700; color: var(--brand-green); line-height: 1.1; }
  .hope-copy .promise { font-size: 9.5px; font-weight: 700; color: var(--brand-blue); }

  .contact { position: absolute; left: 0; right: 0; top: 432px; text-align: center; font-size: 12px; }
  .contact dt { color: var(--brand-blue); font-weight: 900; font-size: 11.5px; letter-spacing: .6px; margin-top: 12px; }
  .contact dt:first-child { margin-top: 0; }
  .contact dd { line-height: 1.35; }
  .contact .rule { width: 50px; height: 2px; background: var(--brand-green); margin: 9px auto 0; }

  .web-band { position: absolute; left: 0; right: 0; bottom: 0; height: 42px; background: var(--brand-green); color: var(--paper);
    font-size: 14px; font-weight: 700; letter-spacing: 2px; display: flex; align-items: center; justify-content: center; }

  .cover-title { position: absolute; left: 0; right: 0; top: 26px; text-align: center; color: var(--paper); font-family: "Libre Baskerville", Georgia, serif; font-weight: 700; }
  .cover-title .name { font-size: 38px; line-height: 1.12; display: block; }
  .cover-title .tagline { font-size: 19px; display: block; margin-top: 4px; }

  .cover-brand { position: absolute; left: 0; right: 0; top: 500px; text-align: center; }
  .cover-brand .mark { width: 46px; height: 46px; border-radius: 50%; background: var(--brand-blue); margin: 0 auto 14px; }
  .cover-brand .brand-name { font-family: "Libre Baskerville", Georgia, serif; font-weight: 700; font-size: 23px; color: var(--brand-blue); letter-spacing: .5px; }
  .cover-brand .web { font-size: 15px; font-weight: 700; letter-spacing: 2px; margin-top: 4px; }
</style>
</head>
<body>
<main class="brochure">
  <svg class="shapes" width="840" height="646" viewBox="0 0 840 646">
    <defs>
      <linearGradient id="wheat-field" x1="0" y1="0" x2="0" y2="1">
        <stop offset="0" stop-color="#f3ead0"/>
        <stop offset=".45" stop-color="#f8f5ea"/>
        <stop offset="1" stop-color="#ffffff"/>
      </linearGradient>
      <linearGradient id="hands-tone" x1="0" y1="0" x2="1" y2="1">
        <stop offset="0" stop-color="#a8c9e6"/>
        <stop offset=".45" stop-color="#c89a7a"/>
        <stop offset="1" stop-color="#d9c2a0"/>
      </linearGradient>
      <linearGradient id="field-tone" x1="0" y1="0" x2="0" y2="1">
        <stop offset="0" stop-color="#0677ba"/>
        <stop offset="1" stop-color="#3f86b8"/>
      </linearGradient>
      <radialGradient id="garden-tone" cx=".5" cy=".5" r=".6">
        <stop offset="0" stop-color="#e9dcc8"/>
        <stop offset=".6" stop-color="#b7a98a"/>
        <stop offset="1" stop-color="#6e8a4c"/>
      </radialGradient>
    </defs>

    <rect class="mid-photo" x="272" y="0" width="278" height="606" fill="url(#wheat-field)" role="img" aria-label="Soft photo of wheat stalks in warm light"/>

    <circle class="title-disc" cx="720" cy="40" r="262" fill="var(--brand-green)"/>

    <rect class="blue-panel" x="0" y="270" width="272" height="376" fill="var(--brand-blue)"/>
    <rect class="field-photo" x="0" y="520" width="272" height="126" fill="url(#field-tone)" role="img" aria-label="Photo of an open field with a lone tree under a blue sky"/>

    <path class="hands-photo" d="M0 0 H452 C470 130 400 270 250 308 C160 330 70 312 0 268 Z"
          fill="url(#hands-tone)" stroke="var(--paper)" stroke-width="6" role="img" aria-label="Photo of a younger hand holding an older person's hand"/>

    <circle class="photo-ring" cx="722" cy="329" r="140" fill="var(--brand-blue)"/>
    <circle class="garden-photo" cx="740" cy="329" r="122" fill="url(#garden-tone)" stroke="var(--paper)" stroke-width="5" role="img" aria-label="Photo of a smiling older woman potting white flowers"/>
  </svg>

  <section class="panel panel-inside-left">
    <div class="brain-copy">
      <p class="kicker">YOU CAN CHANGE YOUR</p>
      <h2 class="headline">BRAIN HEALTH</h2>
      <p class="body">You may believe there is nothing you can do to prevent or treat cognitive decline and Alzheimer's disease. Maybe the idea of a personalized plan to prevent or reverse Alzheimer's sounds like 'snake oil' or wishful thinking. Lumen Ridge can show you reputable science has opened new doors and created an unprecedented opportunity to change your brain health.</p>
      <p class="closing">YES! YOUR BRAIN CAN CHANGE!</p>
    </div>
  </section>

  <section class="panel panel-inside-mid">
    <div class="hope-copy">
      <p class="myth">THERE IS NOTHING WE CAN DO</p>
      <p class="myth-line">Alzheimer's is a fatal disease</p>
      <p class="rebuttal">NOT TRUE!</p>
      <p class="promise">We see people's lives change every day!!!!</p>
    </div>
    <dl class="contact">
      <dt>ADDRESS</dt>
      <dd>100 Example Way<br>Harbor Town, ND</dd>
      <dd class="rule"></dd>
      <dt>PHONE</dt>
      <dd>555-010-2040</dd>
      <dd class="rule"></dd>
      <dt>EMAIL</dt>
      <dd>info@lumenridge-example.org</dd>
    </dl>
    <div class="web-band">www.lumenridge-example.org</div>
  </section>

  <section class="panel panel-cover">
    <h1 class="cover-title">
      <span class="name">LUMEN<br>RIDGE</span>
      <span class="tagline">IS HERE TO HELP!</span>
    </h1>
    <div class="cover-brand">
      <div class="mark"></div>
      <p class="brand-name">LUMEN RIDGE</p>
      <p class="web">www.lumenridge-example.org</p>
    </div>
  </section>
</main>
</body>
</html>
```